New AI Company Needs a Powerpoint

We are a new type of AI company called KestrovaAI. Our AI uses human inspired approaches and put the human on the center of all our solutions. We need a standard company powerpoint design to use with potential investors, customers and partners to introduce our company and explain how the approach we take to AI is very different than others.
We want a design that is clean, modern, and playful. We do not want it to look overly robotic or cliche techy. Our mission is to remind the world that technology is a tool to be used to enhance and assist not to replace real humans.
We want a design that can show boring things (like financial info) in engaging ways.

Please use colors in logo variations along with a vibrant complementary color palette of your choosing,

Industry/Entity Type

Technology

Font styles to use
Sans Serif
Other font styles liked:
• Opensans

Colors
0054AA
0677BA
7BADD7
CADEEF
E8F1F8
0094D4
00A9DD
6FCCEA
C7EBF8
E9F6FB
00AB8E
00BBA5
67D7C9
C6EFE9
E9F9F6
59FF00
82FF00
B8FF75
E3FFCB
F4FFEA

Requirements
Must have
• Must incorporate logo colors and style

```html
<!DOCTYPE html>
<html lang="en">
<head>
<meta charset="utf-8">
<title>KestrovaAI – Company Presentation</title>
<link href="https://fonts.googleapis.com/css2?family=Lato:wght@700;900&family=Open+Sans:wght@400;600;700&display=swap" rel="stylesheet">
<style>
:root{
  --navy:#151a33;
  --navy-deep:#0f1428;
  --blue:#1d8fc6;
  --blue-dark:#0c3f66;
  --ink:#2b2f3a;
  --text:#5d6270;
  --white:#ffffff;
  --canvas:#e6e6e6;
}
*{box-sizing:border-box;margin:0;padding:0}
html,body{width:1200px;height:4051px;overflow:hidden}
body{background:var(--canvas);font-family:"Open Sans",Arial,sans-serif;color:var(--text);position:relative}
.slide{position:absolute;left:76px;width:1048px;height:588px;overflow:hidden;background:var(--white);box-shadow:0 4px 14px rgba(0,0,0,.22)}
.abs{position:absolute}
.photo{position:absolute}
.heading{font-family:"Lato",Arial,sans-serif;font-weight:900;font-size:31px;letter-spacing:-.5px;color:var(--navy);line-height:1}
.heading .accent{color:var(--blue)}
.body-text{font-size:12.4px;line-height:21.5px;text-align:justify;color:var(--text)}
.brand{position:absolute;display:flex;align-items:center;gap:7px;font-family:"Lato",Arial,sans-serif;font-weight:900;font-size:16px;letter-spacing:.3px;color:var(--navy)}
.brand .mark{width:22px;height:22px;border-radius:50%;background:var(--blue)}
.brand.light{color:var(--white)}

/* Slide 1 */
.s1{top:88px}
.s1 .panel{left:0;top:0;width:524px;height:588px;background:linear-gradient(135deg,#1a3358 0%,#121d3a 60%,#0f1731 100%)}
.s1 .photo{left:524px;top:0;width:524px;height:588px;background:radial-gradient(circle at 70% 40%,#2fb3ad 0%,#165a63 35%,#0e2a35 70%),#0e2a35}
.s1 .photo::after{content:"";position:absolute;left:20px;bottom:0;width:120px;height:150px;background:radial-gradient(circle,#d2452a 0%,rgba(210,69,42,0) 70%)}
.s1 .kicker{left:61px;top:166px;font-family:"Lato",Arial,sans-serif;font-weight:900;font-size:14px;color:var(--white)}
.s1 .title{left:61px;top:192px;font-family:"Lato",Arial,sans-serif;font-weight:900;font-size:35px;color:var(--white)}
.s1 .body-text{color:#e3e8f2;width:332px;left:61px;line-height:19.5px}
.s1 .line{left:61px;top:535px;width:78px;height:1px;background:#c7cedb}
.s1 .socials{left:159px;top:521px;display:flex;gap:6px}
.s1 .socials span{width:28px;height:28px;border-radius:50%;background:var(--white)}
.s1 .stem{left:518px;top:150px;width:8px;height:380px;background:var(--blue);border-radius:4px}
.s1 .badge{left:428px;top:62px;width:190px;height:190px;border-radius:50%;background:var(--white);border:9px solid var(--blue);display:flex;align-items:center;justify-content:center}
.s1 .badge .brand{position:static;font-size:17px}

/* Slide 2 */
.s2{top:738px}
.s2 .photo-main{left:0;top:0;width:524px;height:293px;background:linear-gradient(120deg,#26364e 0%,#3c4a5e 40%,#b0742c 75%,#2a2f3a 100%)}
.s2 .block{left:0;top:293px;width:234px;height:295px;background:var(--blue)}
.s2 .photo-inset{left:58px;top:209px;width:176px;height:183px;border:6px solid var(--white);background:linear-gradient(160deg,#c9d8e4,#6b8aa3)}
.s2 .num{font-family:"Lato",Arial,sans-serif;font-weight:700;font-size:88px;line-height:88px;height:88px;color:transparent;-webkit-text-stroke:2.5px var(--blue)}
.s2 .num.dark{-webkit-text-stroke-color:var(--navy)}
.s2 .note{font-size:12.2px;line-height:21.5px;width:190px;text-align:justify}

/* Slide 3 */
.s3{top:1397px}
.s3 .top{left:0;top:0;width:1048px;height:294px;background:var(--navy)}
.s3 .heading{color:var(--white);left:0;width:1048px;text-align:center;top:46px}
.s3 .intro{left:154px;top:114px;width:740px;text-align:center;color:#e4e7ef;font-size:12.4px;line-height:20px}
.service{position:absolute;top:231px;width:230px;text-align:center}
.service .ring{width:124px;height:124px;margin:0 auto;border-radius:50%;background:var(--white);display:flex;align-items:center;justify-content:center;box-shadow:0 2px 6px rgba(0,0,0,.15)}
.service .dot{width:100px;height:100px;border-radius:50%;background:var(--navy);display:flex;align-items:center;justify-content:center}
.service.alt .dot{background:var(--blue)}
.service h3{margin-top:27px;font-family:"Open Sans",Arial,sans-serif;font-weight:700;font-size:13.6px;color:var(--blue)}
.service.alt h3{color:var(--ink)}
.service p{margin:14px auto 0;width:200px;font-size:12.2px;line-height:20px;color:#4a4f5c}

/* Slide 4 */
.s4{top:2056px}
.s4 .bar{left:0;top:181px;width:20px;height:227px;background:var(--navy)}
.s4 .photo{left:61px;top:60px;width:463px;height:468px;background:linear-gradient(135deg,#e8eef3 0%,#b8c6d2 45%,#5a6f82 100%)}
.s4 .panel{left:594px;top:0;width:454px;height:239px;background:var(--blue)}
.s4 .heading{left:641px;top:171px;color:var(--navy)}
.s4 .heading .accent{color:var(--white)}
.s4 .body-text{left:641px;width:346px}

/* Slide 5 */
.s5{top:2715px;background:linear-gradient(120deg,#131c3a 0%,#16335a 55%,#1a4f80 100%)}
.s5 .heading{left:60px;top:68px;color:var(--white)}
.project{position:absolute;top:167px;width:290px;height:337px;background:var(--white);padding:8px}
.project .thumb{height:162px}
.project h3{margin-top:30px;text-align:center;font-weight:700;font-size:13.6px;color:var(--ink)}
.project .rule{width:48px;height:3px;background:var(--blue);margin:6px auto 0}
.project p{margin-top:12px;text-align:center;font-size:12.2px;line-height:21px;color:#4a4f5c}

/* Slide 6 */
.s6{top:3374px}
.s6 .photo{left:524px;top:0;width:524px;height:293px;background:radial-gradient(circle at 40% 60%,#e07a3a 0%,#5a4a48 25%,#2b3f5c 60%,#1b2a44 100%)}
.s6 .block{left:814px;top:293px;width:234px;height:295px;background:var(--blue)}
.s6 .heading{left:61px;top:125px}
.s6 .body-text{left:61px;top:173px;width:407px}
.benefit{position:absolute;width:330px;height:90px}
.benefit .icon{position:absolute;left:0;top:0;width:90px;height:90px;border-radius:50%;background:var(--white);box-shadow:0 3px 10px rgba(0,0,0,.18);display:flex;align-items:center;justify-content:center}
.benefit h3{position:absolute;left:117px;top:8px;font-weight:700;font-size:13.6px;color:var(--ink)}
.benefit.alt h3{color:var(--blue)}
.benefit p{position:absolute;left:117px;top:33px;width:220px;font-size:12.2px;line-height:20px;color:#4a4f5c}
</style>
</head>
<body>

<!-- Welcome -->
<section class="slide s1">
  <div class="abs panel"></div>
  <div class="photo" role="img" aria-label="Person wearing a VR headset interacting with holographic interface beside robotic arms"></div>
  <div class="abs kicker">WELCOME TO</div>
  <div class="abs title">KESTROVA AI</div>
  <p class="abs body-text" style="top:255px">Lorem ipsum dolor sit amet, consectetur adipiscing elit, sed do eiusmod tempor incididunt ut labore et dolore magna aliqua. Ut enim ad minim veniam, quis nostrud exercitation ullamco laboris nisi ut aliquip ex ea commodo consequat.</p>
  <p class="abs body-text" style="top:364px">Consectetur adipiscing elit, sed do eiusmod tempor incididunt ut labore et dolore magna aliqua. Ut enim ad minim veniam, quis nostrud exercitationea.</p>
  <div class="abs line"></div>
  <div class="abs socials"><span></span><span></span><span></span><span></span></div>
  <div class="abs stem"></div>
  <div class="abs badge"><div class="brand"><span class="mark"></span>KESTROVAAI</div></div>
</section>

<!-- About -->
<section class="slide s2">
  <div class="photo photo-main" role="img" aria-label="Engineer in hard hat viewing a digital dashboard over industrial robots"></div>
  <div class="abs block"></div>
  <div class="photo photo-inset" role="img" aria-label="Two colleagues working at computers in a lab"></div>
  <div class="brand" style="left:845px;top:52px"><span class="mark"></span>KESTROVAAI</div>
  <h2 class="abs heading" style="left:580px;top:122px">ABOUT <span class="accent">KESTROVA AI</span></h2>
  <p class="abs body-text" style="left:580px;top:173px;width:407px">Lorem ipsum dolor sit amet, consectetur adipiscing elit, sed do eiusmod tempor incididunt ut labore et dolore magna aliqua. Ut enim ad minim veniam, quis nostrud exercitation ullamco laboris nisi ut aliquip ex ea commodo consequat.</p>
  <p class="abs body-text" style="left:291px;top:342px;width:696px">Lorem ipsum dolor sit amet, consectetur adipiscing elit, sed do eiusmod tempor incididunt ut labore et dolore magna aliqua. Ut enim ad minim veniam, quis nostrud exercitation ullamco laboris nisi ut aliquip ex ea commodo consequat. Duis aute irure dolor in reprehenderit in voluptate velit esse cillum dolore eu fugiat nulla pariatur. Excepteur sint occaecat cupidatat non proident, sunt in culpa qui officia deserunt mollit anim id est laborum.</p>
  <div class="abs num" style="left:288px;top:460px">01</div>
  <p class="abs note" style="left:421px;top:472px">Lorem ipsum dolor sit amet, con ectetur adipiscing elit, sed do eiusmod tempor.</p>
  <div class="abs num dark" style="left:664px;top:460px">02</div>
  <p class="abs note" style="left:797px;top:472px">Lorem ipsum dolor sit amet, con ectetur adipiscing elit, sed do eiusmod tempor.</p>
</section>

<!-- Services -->
<section class="slide s3">
  <div class="abs top"></div>
  <h2 class="abs heading">OUR <span class="accent">SERVICES</span></h2>
  <div class="brand light" style="left:845px;top:52px"><span class="mark"></span>KESTROVAAI</div>
  <p class="abs intro">Lorem ipsum dolor sit amet, consectetur adipiscing elit, sed do eiusmod tempor incididunt ut labore et dolore magna aliqua. Ut enim ad minim veniam, quis nostrud exercitation ullamco laboris nisi ut aliquip ex ea commodo consequat. Duis aute irure dolor in velit esse cillum dolore eu fugiat nulla pariatur.</p>

  <div class="service" style="left:69px">
    <div class="ring"><div class="dot"><svg width="46" height="46" viewBox="0 0 46 46" fill="none" stroke="#fff" stroke-width="1.6"><circle cx="23" cy="23" r="9"/><ellipse cx="23" cy="23" rx="20" ry="8"/><ellipse cx="23" cy="23" rx="20" ry="8" transform="rotate(60 23 23)"/><ellipse cx="23" cy="23" rx="20" ry="8" transform="rotate(-60 23 23)"/></svg></div></div>
    <h3>LOREM IPSUM DOL</h3>
    <p>Lorem ipsum dolor sit amet, con sec tetur adipiscing elit, sed do eiusmod tempor incididunt labore aliqua.</p>
  </div>
  <div class="service alt" style="left:296px">
    <div class="ring"><div class="dot"><svg width="46" height="46" viewBox="0 0 46 46" fill="none" stroke="#fff" stroke-width="1.6"><path d="M23 8a11 11 0 0 0-6 20v5h12v-5a11 11 0 0 0-6-20z"/><path d="M18 37h10M19 41h8M23 4v-2M8 18H5M41 18h-3"/></svg></div></div>
    <h3>LOREM IPSUM DOL</h3>
    <p>Lorem ipsum dolor sit amet, con sec tetur adipiscing elit, sed do eiusmod tempor incididunt labore aliqua.</p>
  </div>
  <div class="service" style="left:522px">
    <div class="ring"><div class="dot"><svg width="46" height="46" viewBox="0 0 46 46" fill="none" stroke="#fff" stroke-width="1.6"><rect x="12" y="12" width="22" height="22" rx="2"/><rect x="18" y="18" width="10" height="10"/><path d="M17 12V6M23 12V6M29 12V6M17 40v-6M23 40v-6M29 40v-6M12 17H6M12 23H6M12 29H6M40 17h-6M40 23h-6M40 29h-6"/></svg></div></div>
    <h3>LOREM IPSUM DOL</h3>
    <p>Lorem ipsum dolor sit amet, con sec tetur adipiscing elit, sed do eiusmod tempor incididunt labore aliqua.</p>
  </div>
  <div class="service alt" style="left:749px">
    <div class="ring"><div class="dot"><svg width="46" height="46" viewBox="0 0 46 46" fill="none" stroke="#fff" stroke-width="1.6"><circle cx="23" cy="23" r="8"/><path d="M23 15V5M23 31v10M15 23H5M31 23h10M17 17l-7-7M29 29l7 7M29 17l7-7M17 29l-7 7"/><circle cx="23" cy="4" r="2"/><circle cx="23" cy="42" r="2"/><circle cx="4" cy="23" r="2"/><circle cx="42" cy="23" r="2"/></svg></div></div>
    <h3>LOREM IPSUM DOL</h3>
    <p>Lorem ipsum dolor sit amet, con sec tetur adipiscing elit, sed do eiusmod tempor incididunt labore aliqua.</p>
  </div>
</section>

<!-- Solution -->
<section class="slide s4">
  <div class="abs bar"></div>
  <div class="photo" role="img" aria-label="Smiling woman working on a laptop with a network graphic and AI label overlay"></div>
  <div class="abs panel"></div>
  <div class="brand light" style="left:845px;top:52px"><span class="mark"></span>KESTROVAAI</div>
  <h2 class="abs heading">OUR <span class="accent">SOLUTION</span></h2>
  <p class="abs body-text" style="top:285px">Lorem ipsum dolor sit amet, consectetur adipiscing elit, sed do eiusmod tempor incididunt ut labore et dolore magna aliqua. Ut enim ad minim veniam, quis nostrud exercitation ullamco laboris nisi ut aliquip ex ea commodo consequat. Duis aute irure dolor in reprehenderit in voluptate velit esse cillum dolore eu fugiat nulla.</p>
  <p class="abs body-text" style="top:429px">Lorem ipsum dolor sit amet, consectetur adipiscing elit, sed do eiusmod tempor incididunt ut labore et dolore magna aliq nim veniam, quis nostrud exercitation ullamco laboris nisi ut aliquip ex ea commodo consequat.</p>
</section>

<!-- Projects -->
<section class="slide s5">
  <h2 class="abs heading">RECENT <span class="accent">PROJECTS</span></h2>
  <div class="brand light" style="left:845px;top:52px"><span class="mark"></span>KESTROVAAI</div>
  <article class="project" style="left:61px">
    <div class="thumb" role="img" aria-label="Hands typing on a laptop with holographic icons" style="background:linear-gradient(135deg,#2b3a4c,#4f8c96 55%,#1e2a36)"></div>
    <h3>LOREM IPSUM DOL</h3><div class="rule"></div>
    <p>Lorem ipsum dolor sit amet, consectetur ad ipiscing elit, sed do eiusmod tempor inci didunt ut labore et dolore magna aliqua. enim ad minim veniam.</p>
  </article>
  <article class="project" style="left:379px">
    <div class="thumb" role="img" aria-label="Businessman holding a tablet with a glowing AI chip graphic" style="background:linear-gradient(135deg,#0f1a2e,#2f4a6e 55%,#c98a3c)"></div>
    <h3>LOREM IPSUM DOL</h3><div class="rule"></div>
    <p>Lorem ipsum dolor sit amet, consectetur ad ipiscing elit, sed do eiusmod tempor inci didunt ut labore et dolore magna aliqua. enim ad minim veniam.</p>
  </article>
  <article class="project" style="left:696px">
    <div class="thumb" role="img" aria-label="Man in VR headset reaching toward a glowing digital sphere" style="background:linear-gradient(135deg,#1a2a5a,#3b7bc8 50%,#2a1f4a)"></div>
    <h3>LOREM IPSUM DOL</h3><div class="rule"></div>
    <p>Lorem ipsum dolor sit amet, consectetur ad ipiscing elit, sed do eiusmod tempor inci didunt ut labore et dolore magna aliqua. enim ad minim veniam.</p>
  </article>
</section>

<!-- Benefits -->
<section class="slide s6">
  <div class="photo" role="img" aria-label="Engineer with tablet controlling a robotic welding arm with sparks"></div>
  <div class="abs block"></div>
  <div class="brand" style="left:61px;top:55px"><span class="mark"></span>KESTROVAAI</div>
  <h2 class="abs heading">OUR <span class="accent">BENEFITS</span></h2>
  <p class="abs body-text">Lorem ipsum dolor sit amet, consectetur adipiscing elit, sed do eiusmod tempor incididunt ut labore et dolore magna aliqua. Ut enim ad minim veniam, quis nostrud exercitation ullamco laboris nisi ut aliquip ex ea commodo consequat.</p>

  <div class="benefit" style="left:61px;top:331px">
    <div class="icon"><svg width="40" height="40" viewBox="0 0 40 40" fill="none" stroke="#1d8fc6" stroke-width="1.6"><path d="M20 8a9 9 0 0 0-5 16v4h10v-4a9 9 0 0 0-5-16z"/><path d="M16 32h8M17 35h6M20 3v2M6 16H4M36 16h-2M9 6l2 2M31 6l-2 2"/></svg></div>
    <h3>LOREM IPSUM:</h3>
    <p>Lorem ipsum dolor sit amet consecte adipiscing elit sedea.</p>
  </div>
  <div class="benefit alt" style="left:435px;top:331px">
    <div class="icon"><svg width="40" height="40" viewBox="0 0 40 40" fill="none" stroke="#151a33" stroke-width="1.6"><circle cx="20" cy="10" r="5"/><circle cx="9" cy="22" r="4"/><circle cx="31" cy="22" r="4"/><path d="M20 15v10M13 22h14M12 35v-5h16v5"/></svg></div>
    <h3>LOREM IPSUM:</h3>
    <p>Lorem ipsum dolor sit amet consecte adipiscing elit sedea.</p>
  </div>
  <div class="benefit alt" style="left:61px;top:446px">
    <div class="icon"><svg width="40" height="40" viewBox="0 0 40 40" fill="none" stroke="#151a33" stroke-width="1.6"><path d="M4 22l8-8 6 4 4-3 6 3 8 4M10 26l5 5c1 1 3 1 4 0l8-8M18 29l3 3M22 26l3 3"/><circle cx="20" cy="8" r="3"/></svg></div>
    <h3>LOREM IPSUM:</h3>
    <p>Lorem ipsum dolor sit amet consecte adipiscing elit sedea.</p>
  </div>
  <div class="benefit" style="left:435px;top:446px">
    <div class="icon"><svg width="40" height="40" viewBox="0 0 40 40" fill="none" stroke="#1d8fc6" stroke-width="1.6"><circle cx="22" cy="14" r="5"/><path d="M22 4v3M22 21v3M12 14h3M29 14h3M15 7l2 2M27 19l2 2M29 7l-2 2M15 21l2-2"/><path d="M4 30h6l6 3h10l8-5"/></svg></div>
    <h3>LOREM IPSUM:</h3>
    <p>Lorem ipsum dolor sit amet consecte adipiscing elit sedea.</p>
  </div>
</section>

</body>
</html>
```